deceased estate clean ups brochures

we would like a brochure to reresent our business we already have new web site and want to do DL A4 brochure to give out to promote our business we already have logo www.brightmoor.com.au is where you can get all info needed

Target Market(s)

families with loved ones that have past away
people done sizing or needing to decluter

Colors
cadf82
33b8a4
886aae
33a6d7

```html
<!DOCTYPE html>
<html lang="en">
<head>
<meta charset="utf-8">
<title>Brightmoor – Deceased Estate Cleanup Brochure</title>
<link href="https://fonts.googleapis.com/css2?family=Montserrat:wght@600;700&family=Open+Sans:wght@400;600&display=swap" rel="stylesheet">
<style>
  :root{
    --teal:#33b8a4;
    --green:#5aa544;
    --lime:#cadf82;
    --lime-line:#8cc63f;
    --purple:#886aae;
    --ink:#1d1d1d;
    --white:#ffffff;
    --bg:#e6e6e6;
  }
  *{margin:0;padding:0;box-sizing:border-box}
  html,body{width:1200px;height:1200px;overflow:hidden;background:var(--bg)}
  .brochure{position:absolute;left:30px;top:197px;width:1140px;height:806px;background:var(--white);overflow:hidden;box-shadow:0 10px 30px rgba(0,0,0,.18)}
  .brochure-art{position:absolute;inset:0}
  .fold{position:absolute;top:0;bottom:0;width:1px;background:rgba(0,0,0,.06)}
  .fold--one{left:380px}.fold--two{left:760px}

  .why{position:absolute;left:34px;top:225px;width:330px;color:var(--white);font-family:"Open Sans",sans-serif}
  .why-title{font-family:"Montserrat",sans-serif;font-weight:700;font-size:19px;text-align:center;letter-spacing:.5px}
  .why-rule{width:110px;height:2px;background:var(--purple);margin:8px auto 18px}
  .why-list{list-style:none;border-left:1px solid rgba(255,255,255,.8);margin-left:18px;padding-left:28px}
  .why-item{position:relative;margin-bottom:14px}
  .why-item::before{content:"";position:absolute;left:-47px;top:-2px;width:36px;height:36px;background:var(--green);clip-path:polygon(25% 4%,75% 4%,100% 50%,75% 96%,25% 96%,0 50%);border:2px solid var(--white)}
  .why-heading{font-family:"Montserrat",sans-serif;font-weight:700;font-size:12px;text-transform:uppercase;margin-bottom:3px}
  .why-text{font-size:10px;line-height:1.45}

  .contact{position:absolute;left:380px;top:0;width:380px;height:806px;font-family:"Open Sans",sans-serif;color:var(--teal)}
  .brand{position:absolute;display:flex;align-items:center;gap:10px;font-family:"Montserrat",sans-serif;font-weight:700;color:var(--ink);letter-spacing:2px}
  .brand-dot{width:26px;height:26px;border-radius:50%;background:var(--lime-line)}
  .contact .brand{left:70px;top:415px;font-size:30px}
  .contact-address{position:absolute;left:70px;top:470px;font-size:17px}
  .contact-lines{position:absolute;left:70px;top:560px;list-style:none}
  .contact-lines li{display:flex;align-items:center;gap:14px;font-size:17px;margin-bottom:16px}
  .contact-lines svg{width:20px;height:20px;flex:none}

  .cover{position:absolute;left:760px;top:0;width:380px;height:806px}
  .cover .brand{left:55px;top:150px;font-size:30px}
  .cover-title{position:absolute;left:0;right:0;top:720px;text-align:center;font-family:"Montserrat",sans-serif;font-weight:700;font-size:26px;line-height:1.15;color:var(--white);letter-spacing:.5px}
</style>
</head>
<body>
<main class="brochure">
  <svg class="brochure-art" viewBox="0 0 1140 806">
    <rect role="img" aria-label="Photo of a smiling older couple on a garden bench outside a brick home" x="0" y="0" width="760" height="380" fill="#9c6a55"/>
    <path d="M0,150 Q160,150 300,205 L0,205 Z" fill="var(--white)"/>
    <path d="M0,165 Q170,160 290,215 Q340,240 380,300 L380,806 L0,806 Z" fill="var(--teal)"/>
    <path d="M380,806 L380,330 Q470,300 560,350 Q640,385 760,360 L760,806 Z" fill="var(--white)"/>
    <path d="M760,0 H1140 V806 H760 Z" fill="var(--white)"/>
    <path role="img" aria-label="Photo of a consultant shaking hands with an older client at a table" d="M760,300 Q960,285 1140,360 L1140,806 L760,806 Z" fill="#d9ddd6"/>
    <path d="M760,300 Q960,285 1140,360" fill="none" stroke="var(--green)" stroke-width="5"/>
    <path d="M760,500 Q850,640 1140,682 L1140,806 L760,806 Z" fill="var(--lime-line)"/>
    <path d="M760,515 Q850,655 1140,694 L1140,806 L760,806 Z" fill="var(--green)"/>
  </svg>
  <div class="fold fold--one"></div>
  <div class="fold fold--two"></div>

  <section class="why">
    <h2 class="why-title">WHY CHOOSE US</h2>
    <div class="why-rule"></div>
    <ul class="why-list">
      <li class="why-item"><h3 class="why-heading">Quality</h3><p class="why-text">Our goal is to enhance your property and achieve the results you are looking for. We appreciate the trust placed in us to deliver a quality job that meets your expectations.</p></li>
      <li class="why-item"><h3 class="why-heading">Professionalism</h3><p class="why-text">Brightmoor only use quality staff and materials that are “fit for purpose”. We keep a professional approach to every job ensuring all agreed tasks are completed and accounted for.</p></li>
      <li class="why-item"><h3 class="why-heading">Pride</h3><p class="why-text">We take pride in our family approach and care we bring to your loved ones belongings. Whether it is simple house clearing, house repairs or larger renovations your home will be ready for rental or sale.</p></li>
      <li class="why-item"><h3 class="why-heading">Areas Serviced</h3><p class="why-text">Specialising in Melbourne CBD and suburbs including: Coburg, Fawkner, Campbellfield, Craigieburn, St. Kilda, Brighton, Caulfield, Hawthorn, Heidelberg, Watsonia, Richmond, Carlton, Collingwood, Brunswick, South Melbourne, Williamstown, Footscray, Newport, Altona, Sunshine, Essendon, Avondale Heights, St. Albans, Keilor, Taylors Lakes, Sydenham, Diggers Rest, Sunbury, Gisborne</p></li>
    </ul>
  </section>

  <section class="contact">
    <div class="brand"><span class="brand-dot"></span>BRIGHTMOOR</div>
    <p class="contact-address">PO Box 482, Kingsford 3099</p>
    <ul class="contact-lines">
      <li><svg viewBox="0 0 24 24"><path d="M6 2h4l2 5-3 2a12 12 0 0 0 6 6l2-3 5 2v4a2 2 0 0 1-2 2A18 18 0 0 1 4 4a2 2 0 0 1 2-2z" fill="var(--green)"/></svg>0400 318 264</li>
      <li><svg viewBox="0 0 24 24"><rect x="4" y="9" width="16" height="11" rx="2" fill="var(--green)"/><path d="M2 9c3-5 17-5 20 0l-4 1-2-3H8L6 10z" fill="var(--green)"/></svg>0400 318 264</li>
      <li><svg viewBox="0 0 24 24"><rect x="2" y="5" width="20" height="14" fill="none" stroke="var(--green)" stroke-width="1.6"/><path d="M2 5l10 8 10-8" fill="none" stroke="var(--green)" stroke-width="1.6"/></svg>info@brightmoor.com.au</li>
    </ul>
  </section>

  <section class="cover">
    <div class="brand"><span class="brand-dot"></span>BRIGHTMOOR</div>
    <h1 class="cover-title">DECEASED ESTATE<br>CLEANSUP</h1>
  </section>
</main>
</body>
</html>
```